Business cards to launch an education platform

Hi,
I am looking at having new business cards designed.
I am a startup, developing a web platform for schools and university, the education world. It's an online assessment system.
I would like a card that looks classy, and that is using the colors and the font of my logo.

I have attached:
1) my logo
2) A business card that I have designed quickly so you can have all the information required in the card, but I really don't like it.
3) The font that I am using (Lato Regular) to design my web platform
4) Some screenshots of my web platform so you can have a look at the style that I have.

Target Market(s)

Major market: Education system: Schools and university
Minor markets: Business in general

Industry/Entity Type

Business

Contact Information for Business Card

Clara Fenwick
Director

M: 0437 518 902
E: clara.fenwick@amberLoomSystems.com.au

Requirements
Must have
• The colors of my logo

```html
<!DOCTYPE html>
<html lang="en">
<head>
<meta charset="utf-8">
<title>Amber Loom Systems – Business Cards</title>
<link rel="stylesheet" href="https://fonts.googleapis.com/css2?family=Lato:wght@400;700&display=swap">
<style>
  :root {
    --backdrop: #e9eaec;
    --card-white: #f3f3f4;
    --navy: #0b3d73;
    --navy-deep: #082f5c;
    --blue-mid: #0f5fa6;
    --cyan: #2cc3e0;
    --cyan-soft: #3fb6d8;
    --ink: #3a3a3e;
    --white: #ffffff;
  }
  * { box-sizing: border-box; margin: 0; padding: 0; }
  html, body {
    width: 1105px;
    height: 1200px;
    overflow: hidden;
    background: var(--backdrop);
    font-family: "Lato", sans-serif;
  }
  .canvas {
    position: relative;
    width: 1105px;
    height: 1200px;
  }
  .card {
    position: absolute;
    left: 180px;
    width: 745px;
    height: 425px;
    overflow: hidden;
  }

  /* Front */
  .card-front {
    top: 120px;
    background: var(--card-white);
  }
  .name-band {
    position: absolute;
    left: 0;
    top: 58px;
    width: 430px;
    height: 118px;
    background: var(--navy);
    padding: 28px 0 0 52px;
    color: var(--white);
  }
  .holder-name {
    font-weight: 700;
    font-size: 26px;
    letter-spacing: 0.3px;
    text-transform: uppercase;
  }
  .holder-role {
    margin-top: 4px;
    font-size: 18px;
    text-transform: uppercase;
  }
  .brand-mark {
    position: absolute;
    left: 448px;
    top: 76px;
    display: flex;
    align-items: center;
    gap: 14px;
  }
  .brand-square {
    width: 58px;
    height: 58px;
    background: var(--blue-mid);
  }
  .brand-name {
    font-size: 27px;
    font-weight: 400;
    color: var(--navy);
    letter-spacing: 0.5px;
    line-height: 1.1;
    width: 200px;
  }
  .contact {
    position: absolute;
    left: 0;
    right: 0;
    top: 318px;
    text-align: center;
    color: var(--ink);
  }
  .contact-phone {
    font-weight: 700;
    font-size: 19px;
    letter-spacing: 0.5px;
  }
  .contact-email {
    margin-top: 8px;
    font-size: 19px;
  }

  /* Back */
  .card-back {
    top: 640px;
    background: linear-gradient(160deg, var(--navy-deep) 0%, var(--blue-mid) 45%, var(--navy) 100%);
  }
  .back-decoration {
    position: absolute;
    inset: 0;
    background:
      radial-gradient(ellipse at 75% 85%, rgba(44, 195, 224, 0.45) 0%, rgba(44, 195, 224, 0) 55%),
      radial-gradient(ellipse at 40% 30%, rgba(60, 140, 210, 0.35) 0%, rgba(60, 140, 210, 0) 60%);
  }
  .back-content {
    position: absolute;
    left: 0;
    right: 0;
    top: 150px;
    text-align: center;
    color: var(--cyan);
  }
  .back-brand {
    font-size: 50px;
    font-weight: 400;
    letter-spacing: 4px;
  }
  .back-web {
    margin-top: 10px;
    font-size: 22px;
    letter-spacing: 1.5px;
  }
  .tagline {
    position: absolute;
    left: 0;
    right: 0;
    top: 340px;
    text-align: center;
    font-size: 20px;
    color: var(--cyan-soft);
  }
  .tagline .dot { margin: 0 8px; }
</style>
</head>
<body>
<main class="canvas">

  <section class="card card-front" aria-label="Business card front">
    <div class="name-band">
      <p class="holder-name">Clara Fenwick</p>
      <p class="holder-role">Director</p>
    </div>
    <div class="brand-mark">
      <span class="brand-square"></span>
      <span class="brand-name">Amber Loom Systems</span>
    </div>
    <div class="contact">
      <p class="contact-phone">0437 518 902</p>
      <p class="contact-email">clara.fenwick@amberLoomSystems.com.au</p>
    </div>
  </section>

  <section class="card card-back" aria-label="Business card back">
    <div class="back-decoration" role="img" aria-label="Large faint brand symbol decoration in blue tones"></div>
    <div class="back-content">
      <p class="back-brand">Amber Loom Systems</p>
      <p class="back-web">amberLoomSystems.com.au</p>
    </div>
    <p class="tagline">Lorem ipsum dolor<span class="dot">•</span>Wisi mandamus<span class="dot">•</span>Vix cu discere</p>
  </section>

</main>
</body>
</html>
```